Animal Eye Clinic needs a Business card

We are a new veterinary ophthalmology practice (Ridgeline Pet Vision Care) and we need a business card designed. We only see animal eyes - we are not a regular veterinary clinic. We already have a logo. We are looking for a professional, good looking business card to hand out to our clients. We are looking for something simple but professional and contemporary. Our logo is likely the only picture/graphic that needs to be on the card.
Updates

Contact Information for Business Card

Delia Vossman, BSc, DVM, MSc, DipACVO
Veterinary Ophthalmologist

Phone: 250.418.3927
Email: ridgelinepetvisioncare@mailbox-example.net
Website: ridgelinepetvisioncare-example.net
Address: 1874 Thornbury Rd
Kelowna, BC, V1X 4M9

Colors

Designer to choose colors to be used in the design.

Requirements
Must have
• Our logo (attached)

```html
<!DOCTYPE html>
<html lang="en">
<head>
<meta charset="utf-8">
<title>Ridgeline Pet Vision Care – Business Card</title>
<link rel="stylesheet" href="https://fonts.googleapis.com/css2?family=Open+Sans:wght@400;600;700&display=swap">
<style>
  :root {
    --backdrop: #c9c8c9;
    --card-black: #000000;
    --teal: #0895a8;
    --stripe-grey: #7a7a7a;
    --text-white: #ffffff;
    --text-soft: #e6e6e6;
  }
  * { box-sizing: border-box; margin: 0; padding: 0; }
  html, body {
    width: 1008px;
    height: 1200px;
    overflow: hidden;
  }
  body {
    background: var(--backdrop);
    font-family: "Open Sans", Arial, sans-serif;
    position: relative;
  }
  .card {
    position: absolute;
    left: 86px;
    width: 836px;
    height: 478px;
    background: var(--card-black);
    overflow: hidden;
    box-shadow: 10px 12px 14px rgba(0, 0, 0, 0.45);
  }
  .card--front { top: 84px; }
  .card--back { top: 642px; }
  .card__waves {
    position: absolute;
    inset: 0;
    width: 100%;
    height: 100%;
  }
  .brand-name {
    position: absolute;
    font-weight: 700;
    font-size: 26px;
    line-height: 1.15;
    letter-spacing: 0.5px;
    text-transform: uppercase;
  }
  .card--front .brand-name {
    left: 64px;
    top: 86px;
    color: var(--text-white);
  }
  .card--back .brand-name {
    left: 460px;
    top: 76px;
    color: var(--teal);
  }
  .brand-emblem {
    position: absolute;
    border-radius: 50%;
    background: var(--teal);
  }
  .card--front .brand-emblem {
    left: 508px;
    top: 156px;
    width: 264px;
    height: 264px;
  }
  .card--back .brand-emblem {
    left: 136px;
    top: 48px;
    width: 252px;
    height: 252px;
  }
  .role {
    position: absolute;
    left: 61px;
    top: 327px;
    width: 356px;
    color: var(--text-white);
  }
  .role__title {
    font-size: 25px;
    font-weight: 600;
    padding-bottom: 10px;
    border-bottom: 2px dotted var(--text-soft);
  }
  .role__name {
    margin-top: 10px;
    font-size: 18px;
    font-weight: 400;
  }
  .contact-list {
    position: absolute;
    left: 460px;
    top: 198px;
    list-style: none;
    color: var(--text-white);
    font-size: 15px;
    font-weight: 600;
  }
  .contact-list li {
    display: flex;
    align-items: center;
    gap: 12px;
    height: 29px;
  }
  .contact-list svg {
    width: 14px;
    height: 14px;
    flex: none;
  }
</style>
</head>
<body>

  <section class="card card--front" aria-label="Business card front">
    <svg class="card__waves" viewBox="0 0 836 478" preserveAspectRatio="none" aria-hidden="true">
      <path d="M0 0 H836 V62 C700 80 560 110 430 175 C300 240 150 270 0 255 Z" fill="var(--stripe-grey)"/>
      <path d="M0 0 H836 V38 C700 55 560 90 430 155 C300 225 150 262 0 250 Z" fill="var(--teal)"/>
    </svg>
    <div class="brand-name">Ridgeline<br>Pet Vision Care</div>
    <div class="brand-emblem" role="img" aria-label="Clinic emblem area"></div>
    <div class="role">
      <p class="role__title">Veterinary Ophthalmologist</p>
      <p class="role__name">Delia Vossman, BSc, DVM, MSc, DipACVO</p>
    </div>
  </section>

  <section class="card card--back" aria-label="Business card back">
    <svg class="card__waves" viewBox="0 0 836 478" preserveAspectRatio="none" aria-hidden="true">
      <path d="M0 355 C180 300 330 330 470 350 C620 372 740 350 836 318 V478 H0 Z" fill="var(--stripe-grey)"/>
      <path d="M0 372 C180 320 330 345 470 365 C620 388 740 372 836 340 V478 H0 Z" fill="var(--teal)"/>
    </svg>
    <div class="brand-emblem" role="img" aria-label="Clinic emblem area"></div>
    <div class="brand-name">Ridgeline<br>Pet Vision Care</div>
    <ul class="contact-list">
      <li>
        <svg viewBox="0 0 24 24" aria-hidden="true"><path fill="#fff" d="M6.6 10.8a15.1 15.1 0 0 0 6.6 6.6l2.2-2.2c.3-.3.7-.4 1-.2 1.1.4 2.3.6 3.6.6.6 0 1 .4 1 1V20c0 .6-.4 1-1 1A17 17 0 0 1 3 4c0-.6.4-1 1-1h3.5c.6 0 1 .4 1 1 0 1.3.2 2.5.6 3.6.1.3 0 .7-.2 1z"/></svg>
        <span>250.418.3927</span>
      </li>
      <li>
        <svg viewBox="0 0 24 24" aria-hidden="true"><g fill="none" stroke="#fff" stroke-width="2"><circle cx="12" cy="12" r="9"/><path d="M3 12h18M12 3c3 3 3 15 0 18M12 3c-3 3-3 15 0 18"/></g></svg>
        <span>ridgelinepetvisioncare@mailbox-example.net</span>
      </li>
      <li>
        <svg viewBox="0 0 24 24" aria-hidden="true"><g fill="none" stroke="#fff" stroke-width="2.4"><circle cx="12" cy="12" r="9"/><path d="M7 12h10"/></g></svg>
        <span>ridgelinepetvisioncare-example.net</span>
      </li>
      <li>
        <svg viewBox="0 0 24 24" aria-hidden="true"><path fill="#fff" d="M12 2a7 7 0 0 0-7 7c0 5 7 13 7 13s7-8 7-13a7 7 0 0 0-7-7zm0 9.5A2.5 2.5 0 1 1 12 6.5a2.5 2.5 0 0 1 0 5z"/></svg>
        <span>1874 Thornbury Rd Kelowna, BC, V1X 4M9</span>
      </li>
    </ul>
  </section>

</body>
</html>
```